Orvane Mechanical - Letterhead

We are a plumbing and hvac company based in Calgary. This letterhead will be on our quotes, invoices, preventative maintenance proposals etc.

```html
<!DOCTYPE html>
<html lang="en">
<head>
<meta charset="utf-8">
<title>Orvane Mechanical – Letterhead</title>
<link rel="stylesheet" href="https://fonts.googleapis.com/css2?family=Work+Sans:wght@400;700&display=swap">
<style>
  :root {
    --backdrop: #e4e1dd;
    --paper: #ffffff;
    --pattern-tint: #f4f4f5;
    --brand-blue: #1f6fb8;
    --brand-orange: #e8622a;
    --ink: #3a3a3a;
  }
  * { box-sizing: border-box; margin: 0; padding: 0; }
  html, body {
    width: 1185px;
    height: 1200px;
    overflow: hidden;
    background: var(--backdrop);
    font-family: "Work Sans", Arial, sans-serif;
  }
  .letterhead {
    position: absolute;
    left: 182px;
    top: 20px;
    width: 820px;
    height: 1160px;
    background: var(--paper);
    box-shadow: 0 2px 8px rgba(0,0,0,0.18);
    overflow: hidden;
  }
  .letterhead__pattern {
    position: absolute;
    inset: 0;
    background: linear-gradient(180deg, var(--pattern-tint), #f8f8f9);
  }
  .brand {
    position: absolute;
    top: 48px;
    left: 0;
    right: 0;
    display: flex;
    flex-direction: column;
    align-items: center;
    color: var(--brand-blue);
    font-weight: 700;
  }
  .brand__mark {
    width: 68px;
    height: 68px;
    border-radius: 50%;
    background: var(--brand-orange);
    margin-bottom: 22px;
  }
  .brand__name {
    font-size: 34px;
    letter-spacing: 1px;
    line-height: 1;
  }
  .brand__sub {
    font-size: 13px;
    letter-spacing: 2px;
    margin-top: 8px;
  }
  .footer-rule {
    position: absolute;
    left: 79px;
    width: 663px;
    top: 1042px;
    height: 1.5px;
    background: var(--brand-orange);
  }
  .contact {
    position: absolute;
    top: 1076px;
    font-size: 12.5px;
    line-height: 16.5px;
    color: var(--ink);
    letter-spacing: 0.3px;
  }
  .contact--left { left: 79px; }
  .contact--right { right: 78px; top: 1092.5px; text-align: right; }
  .contact__line { display: flex; align-items: center; gap: 4px; }
  .contact__icon { width: 9px; height: 9px; flex: none; }
</style>
</head>
<body>
  <main class="letterhead">
    <div class="letterhead__pattern" role="img" aria-label="Faint repeating brand-symbol pattern across the sheet"></div>

    <header class="brand">
      <div class="brand__mark"></div>
      <div class="brand__name">ORVANE</div>
      <div class="brand__sub">MECHANICAL INC</div>
    </header>

    <div class="footer-rule"></div>

    <address class="contact contact--left" style="font-style:normal">
      <div class="contact__line">
        <svg class="contact__icon" viewBox="0 0 10 10"><path d="M2 0.8 L3.6 2.8 L2.8 3.8 Q4 6.4 6.2 7.2 L7.2 6.4 L9.2 8 L8 9.4 Q2.8 8.8 0.6 2 Z" fill="var(--brand-blue)"/></svg>
        <span>(403) 555-0182</span>
      </div>
      <div class="contact__line">
        <svg class="contact__icon" viewBox="0 0 10 10"><rect x="0.8" y="2" width="8.4" height="6" fill="none" stroke="var(--brand-blue)" stroke-width="1"/><path d="M0.8 2 L5 5.5 L9.2 2" fill="none" stroke="var(--brand-blue)" stroke-width="1"/></svg>
        <span>info@orvanemech.com</span>
      </div>
      <div class="contact__line">
        <svg class="contact__icon" viewBox="0 0 10 10"><circle cx="5" cy="5" r="4.2" fill="none" stroke="var(--brand-blue)" stroke-width="0.9"/><ellipse cx="5" cy="5" rx="1.8" ry="4.2" fill="none" stroke="var(--brand-blue)" stroke-width="0.8"/><path d="M0.8 5 H9.2" stroke="var(--brand-blue)" stroke-width="0.8"/></svg>
        <span>www.orvanemech.com</span>
      </div>
    </address>

    <address class="contact contact--right" style="font-style:normal">
      <div>2210 Larchwood Road NE</div>
      <div>Calgary, AB T2E 6K4</div>
    </address>
  </main>
</body>
</html>
```